This is for a Logo / Graphic Design Packaging. Cannabis Product Line.
Pease see description for more details
Updates

Reason: Currently Seeking in depth Revisions of submissions as well as giving a few new designers a chance to submit their work. Thank you for your patience and we will keep in close contact. Thank You All!!

Target Market(s)

Cannabis Smokers

Industry/Entity Type

Graphic Design

Requirements
Must have
• Create Logo: Drift Lumen
• Sub-Brand: Palvinks
• Drift Lumen must be at top.
• with "Palvinks" below logo or on the bottom of cigar pouch.
• Product: 3 Pack of Cannabis Cigars
• I would like it to to be a scenery that covers the front and back of the packaging.
• Drift Lumen across the top in a Spacey Font with Galaxy and camp fire burning at the bottom. Maybe Little Cannabis and Alien Fairlys flying around. On the Backside have a few UFO's .. use your creative imagination and run with it. Please. And feel free to ask me any questions I will respond as soon as I can.

```html
<!DOCTYPE html>
<html lang="en">
<head>
<meta charset="utf-8">
<title>Drift Lumen – Palvinks Hemp Cigars Pouch</title>
<link href="https://fonts.googleapis.com/css2?family=Orbitron:wght@700;900&family=Michroma&display=swap" rel="stylesheet">
<style>
  :root {
    --page-bg: #f4f4f4;
    --galaxy-green: #1f8a3c;
    --galaxy-bright: #3fbf58;
    --galaxy-deep: #0b3d1a;
    --space-black: #040504;
    --title-light: #eafbd8;
    --moon-pale: #cfdcc8;
    --flare-core: #fffbe8;
    --flare-gold: #f7e6a6;
    --fire-orange: #e8761a;
    --fire-deep: #6a2408;
    --ink: #050505;
    --crimp-line: rgba(255,255,255,0.16);
  }
  * { margin: 0; padding: 0; box-sizing: border-box; }
  html, body {
    width: 1200px; height: 978px; overflow: hidden;
    background: var(--page-bg);
  }
  .canvas { position: relative; width: 1200px; height: 978px; }
  .pouch {
    position: absolute; left: 358px; top: 116px;
    width: 482px; height: 698px;
    overflow: hidden;
    background: var(--space-black);
    box-shadow: 0 10px 30px rgba(0,0,0,0.18);
  }
  .galaxy-scene {
    position: absolute; left: 0; right: 0; top: 0; height: 470px;
    background:
      radial-gradient(ellipse at 72% 48%, rgba(200,210,200,0.4) 0, transparent 30%),
      radial-gradient(ellipse at 35% 40%, var(--galaxy-bright) 0, transparent 55%),
      linear-gradient(180deg, var(--galaxy-deep) 0%, var(--galaxy-green) 38%, #145c28 65%, var(--space-black) 100%);
  }
  .moon {
    position: absolute; left: 0; top: 0; width: 98px; height: 92px;
    background: radial-gradient(ellipse at 30% 30%, #e4ede0 0, var(--moon-pale) 55%, #9fb59a 100%);
    border-bottom-right-radius: 70px 70px;
  }
  .fairy-scene {
    position: absolute; left: 20px; right: 20px; top: 216px; height: 200px;
    background: linear-gradient(180deg, rgba(5,25,10,0.35) 0%, rgba(3,12,5,0.7) 55%, rgba(4,5,4,0.9) 100%);
    border-radius: 12px;
  }
  .crimp {
    position: absolute; left: 0; right: 0; height: 60px;
    background: repeating-linear-gradient(180deg, var(--crimp-line) 0 1px, transparent 1px 6px);
  }
  .crimp--top { top: 0; }
  .crimp--bottom { bottom: 0; background: repeating-linear-gradient(180deg, rgba(255,255,255,0.05) 0 1px, transparent 1px 6px); }
  .brand-title {
    position: absolute; top: 90px; left: 0; right: 0;
    text-align: center;
    font-family: "Orbitron", sans-serif; font-weight: 900;
    color: var(--title-light);
    text-transform: uppercase;
    line-height: 1;
  }
  .brand-title__line { display: block; }
  .brand-title__line--top { font-size: 42px; letter-spacing: 6px; }
  .brand-title__line--bottom { font-size: 52px; letter-spacing: 10px; margin-top: 4px; }
  .fire-area {
    position: absolute; left: 112px; top: 430px; width: 260px; height: 260px;
    background: radial-gradient(circle at 50% 50%, var(--fire-orange) 0, #b8480f 40%, var(--fire-deep) 62%, transparent 72%);
    opacity: 0.9;
  }
  .light-flare {
    position: absolute; left: -30px; top: 510px; width: 542px; height: 90px;
    background: radial-gradient(ellipse at 50% 50%, var(--flare-core) 0, var(--flare-gold) 28%, rgba(247,230,166,0.35) 55%, transparent 72%);
  }
  .product-name {
    position: absolute; top: 530px; left: 0; right: 0; text-align: center;
    font-family: "Orbitron", sans-serif; font-weight: 900;
    font-size: 36px; letter-spacing: 3px; line-height: 1;
    color: var(--ink); text-transform: uppercase;
  }
  .product-type {
    position: absolute; top: 572px; left: 0; right: 0; text-align: center;
    font-family: "Michroma", sans-serif;
    font-size: 17px; letter-spacing: 4px; line-height: 1;
    color: var(--ink); text-transform: uppercase;
  }
</style>
</head>
<body>
<main class="canvas">
  <section class="pouch">
    <div class="galaxy-scene" role="img" aria-label="Green nebula starfield sky"></div>
    <div class="moon" role="img" aria-label="Pale cratered moon in the top corner"></div>
    <div class="fairy-scene" role="img" aria-label="Dark silhouettes of winged fairies flying in the night sky"></div>
    <div class="crimp crimp--top"></div>
    <h1 class="brand-title">
      <span class="brand-title__line brand-title__line--top">Drift</span>
      <span class="brand-title__line brand-title__line--bottom">Lumen</span>
    </h1>
    <div class="fire-area" role="img" aria-label="Ring of burning fire with flying embers"></div>
    <div class="light-flare"></div>
    <p class="product-name">Palvinks</p>
    <p class="product-type">Hemp Cigars</p>
    <div class="crimp crimp--bottom"></div>
  </section>
</main>
</body>
</html>
```